****Business Card Design for Quarrystone Development. Design based around attached logo/company name

I’m looking for business card design for my company Quarrystone Development Group,LLC. Design should be professional, sharp and minimal. Outside of the attached logos, greyscale colors for remainder of cards. My thoughts are two-sided card with attached logo on one side and my info on the other but open to one-sided as well with right design.
Target Market(s)
Real estate professionals including banks, private investors, property owners, developers, commercial tenants like Brewlantern, Grovika or Tanquist’s.
Industry/Entity Type
Commercial real estate development and investments.
Contact Information for Business Card
Name, title, email, phone #’s, web address and physical address
Font styles to use
Other font styles liked:
- Helvetica, Garamond, etc
Colors
Designer to choose only greyscale colors for use in the design.
Requirements
Must have
- Attached logo first or second options.
Nice to have
- Two sided card with logo on one side. Attached Logo/company name can be laid out any way that flows as long as it’s legible.name
Should not have
- No loud colors. ***Please do not include logo, I have removed the company design with a logo image.

```html
<!DOCTYPE html>
<html lang="en">
<head>
<meta charset="utf-8">
<title>Quarrystone Development Group, LLC — Business Card</title>
<link rel="stylesheet" href="https://fonts.googleapis.com/css2?family=Cinzel:wght@400;700&family=Arimo:wght@400&display=swap">
<style>
  :root {
    --page-bg: #e4e5e8;
    --card-dark: #4b505d;
    --card-dark-text: #9a9ea8;
    --card-light: #ffffff;
    --ink: #5c6272;
    --ink-soft: #6d7280;
    --band: #777c8b;
    --stripe: #b3b5ba;
    --rule: #8d9099;
  }
  * { box-sizing: border-box; margin: 0; padding: 0; }
  html, body { width: 1200px; height: 901px; overflow: hidden; }
  body {
    background: var(--page-bg);
    font-family: "Arimo", Helvetica, Arial, sans-serif;
    position: relative;
  }
  .card {
    position: absolute;
    top: 302px;
    width: 525px;
    height: 300px;
    box-shadow: 0 10px 28px rgba(0,0,0,0.18);
    overflow: hidden;
  }
  /* Front: company name on dark stock */
  .card-front {
    left: 45px;
    background: var(--card-dark);
    display: flex;
    align-items: center;
    justify-content: center;
  }
  .wordmark {
    color: var(--card-dark-text);
    font-family: "Cinzel", Georgia, serif;
    font-weight: 400;
    text-align: center;
    line-height: 1;
  }
  .wordmark-name { font-size: 44px; letter-spacing: 2px; }
  .wordmark-sub {
    display: block;
    margin-top: 8px;
    padding-top: 6px;
    border-top: 1px solid var(--card-dark-text);
    font-size: 15px;
    letter-spacing: 3px;
  }
  /* Back: contact details on white stock */
  .card-back {
    left: 630px;
    background: var(--card-light);
    color: var(--ink);
  }
  .company {
    position: absolute;
    left: 30px;
    top: 34px;
    font-family: "Cinzel", Georgia, serif;
    font-weight: 400;
    color: var(--ink-soft);
    line-height: 1;
  }
  .company-name { font-size: 27px; letter-spacing: 1px; }
  .company-sub {
    display: block;
    margin-top: 5px;
    padding-top: 4px;
    border-top: 1px solid var(--rule);
    font-size: 10.5px;
    letter-spacing: 1.6px;
  }
  .rule {
    position: absolute;
    left: 30px;
    right: 30px;
    top: 160px;
    height: 1px;
    background: var(--rule);
  }
  .person { position: absolute; left: 30px; top: 118px; }
  .person-name {
    font-family: "Cinzel", Georgia, serif;
    font-weight: 700;
    font-size: 19px;
    letter-spacing: 1px;
    line-height: 1;
  }
  .person-title { font-size: 13px; margin-top: 4px; color: var(--ink-soft); }
  .address {
    position: absolute;
    left: 30px;
    top: 178px;
    font-size: 13.5px;
    line-height: 1.4;
    color: var(--ink-soft);
  }
  .contacts {
    position: absolute;
    right: 30px;
    top: 78px;
    list-style: none;
    font-size: 13px;
    line-height: 1.55;
    text-align: right;
    color: var(--ink);
  }
  .contacts li { display: flex; align-items: center; justify-content: flex-end; gap: 8px; }
  .contacts svg { width: 11px; height: 11px; flex: none; }
  .band { position: absolute; left: 0; bottom: 0; width: 525px; height: 110px; }
</style>
</head>
<body>

<section class="card card-front" aria-label="Card front">
  <h1 class="wordmark">
    <span class="wordmark-name">QUARRYSTONE</span>
    <span class="wordmark-sub">DEVELOPMENT GROUP, LLC</span>
  </h1>
</section>

<section class="card card-back" aria-label="Card back">
  <svg class="band" viewBox="0 0 525 110" preserveAspectRatio="none" aria-hidden="true">
    <path d="M0 96 L320 96 C345 96 350 62 385 62 L525 62 L525 110 L0 110 Z" fill="var(--stripe)"/>
    <path d="M0 102 L326 102 C352 102 358 68 392 68 L525 68 L525 110 L0 110 Z" fill="var(--card-light)"/>
    <path d="M0 105 L330 105 C356 105 362 72 396 72 L525 72 L525 110 L0 110 Z" fill="var(--band)"/>
  </svg>

  <div class="company">
    <span class="company-name">QUARRYSTONE</span>
    <span class="company-sub">DEVELOPMENT GROUP, LLC</span>
  </div>

  <ul class="contacts">
    <li>(541) 555-0148
      <svg viewBox="0 0 12 12"><path d="M3 1 L5 3.5 L4 5 C5 7 6 8 7.5 8.5 L9 7.5 L11 9.5 L9.5 11 C5 10.5 1.5 7 1 2.5 Z" fill="none" stroke="var(--ink)" stroke-width="1"/></svg>
    </li>
    <li>info@quarrystonegroup.com
      <svg viewBox="0 0 12 12"><rect x="1" y="2.5" width="10" height="7" fill="none" stroke="var(--ink)" stroke-width="1"/><path d="M1 2.5 L6 7 L11 2.5" fill="none" stroke="var(--ink)" stroke-width="1"/></svg>
    </li>
    <li>www.quarrystonegroup.com
      <svg viewBox="0 0 12 12"><circle cx="6" cy="6" r="5" fill="none" stroke="var(--ink)" stroke-width="1"/><ellipse cx="6" cy="6" rx="2.2" ry="5" fill="none" stroke="var(--ink)" stroke-width="0.8"/><path d="M1 6 H11" stroke="var(--ink)" stroke-width="0.8"/></svg>
    </li>
  </ul>

  <div class="person">
    <p class="person-name">DANIEL HARTWELL</p>
    <p class="person-title">Director</p>
  </div>
  <div class="rule" style="top:170px"></div>
  <address class="address" style="top:184px; font-style:normal">
    1187 Ledgerock Lane<br>Millbrook, OR 97350
  </address>
</section>

</body>
</html>
```